"Harbor Builders" is a residential building company and needs a new business card design and may re

We would like a redesign based on the existing logo, and would like to see a new font as well. We are bespoke home builders who build sustainable energy efficient homes.

Industry/Entity Type

Construction

Contact Information for Business Card

Business card size 40mm x 90mm

Colors

Designer to choose colors to be used in the design.

```html
<!DOCTYPE html>
<html lang="en">
<head>
<meta charset="utf-8">
<title>Harbor Builders – Business Card</title>
<link rel="stylesheet" href="https://fonts.googleapis.com/css2?family=Roboto:wght@400;500;700&family=Roboto+Condensed:wght@700&display=swap">
<style>
  :root {
    --lime: #b6d335;
    --ink: #0a0a0b;
    --card-dark: #1b1c1e;
    --paper: #f3f3f3;
    --text: #3c3c3c;
    --rule: #c9c9c9;
    --stage: #e6e4e0;
  }
  * { box-sizing: border-box; margin: 0; padding: 0; }
  html, body { width: 1200px; height: 960px; overflow: hidden; }
  body {
    background: var(--stage);
    position: relative;
    font-family: "Roboto", Arial, sans-serif;
  }
  .card {
    position: absolute;
    width: 600px;
    height: 344px;
    overflow: hidden;
  }
  .card--front { left: 302px; top: 128px; background: var(--paper); }
  .card--back { left: 300px; top: 488px; height: 342px; background: var(--card-dark); }

  .front-band { position: absolute; inset: 0; width: 600px; height: 344px; }
  .holder-name {
    position: absolute;
    top: 70px; left: 0; width: 600px;
    text-align: center;
    font-family: "Roboto Condensed", Arial, sans-serif;
    font-weight: 700;
    font-size: 21px;
    color: var(--lime);
    letter-spacing: 0.2px;
  }
  .brand {
    position: absolute;
    left: 36px; top: 204px;
    display: flex; align-items: center; gap: 12px;
  }
  .brand__mark { width: 22px; height: 22px; background: var(--lime); }
  .brand__name {
    font-family: "Roboto", Arial, sans-serif;
    font-weight: 700;
    font-size: 26px;
    color: var(--ink);
  }
  .divider {
    position: absolute;
    left: 295px; top: 150px;
    width: 1px; height: 165px;
    background: linear-gradient(var(--paper), var(--rule) 20%, var(--rule) 80%, var(--paper));
  }
  .contact {
    position: absolute;
    left: 319px; top: 151px;
    font-size: 14.5px;
    line-height: 18.5px;
    color: var(--text);
  }
  .contact__company { font-weight: 500; }
  .contact__gap { height: 2px; }
  .contact__row { display: flex; align-items: center; gap: 9px; }
  .contact__row svg { width: 13px; height: 13px; flex: none; }
  .contact__row--first { margin-top: 4px; }

  .back-name {
    position: absolute;
    top: 120px; left: 0; width: 600px;
    display: flex; justify-content: center; align-items: center; gap: 18px;
  }
  .back-name__mark { width: 46px; height: 46px; background: var(--lime); }
  .back-name__text {
    font-family: "Roboto", Arial, sans-serif;
    font-weight: 700;
    font-size: 52px;
    color: var(--lime);
  }
  .back-web {
    position: absolute;
    top: 296px; left: 0; width: 600px;
    text-align: center;
    font-size: 14px;
    letter-spacing: 2.6px;
    color: var(--lime);
  }
</style>
</head>
<body>
  <section class="card card--front">
    <svg class="front-band" viewBox="0 0 600 344" aria-hidden="true">
      <polygon points="0,0 600,0 600,86 300,126 0,86" fill="var(--lime)"/>
      <polygon points="0,0 600,0 600,80 300,118 0,80" fill="var(--ink)"/>
      <polygon points="0,0 600,0 300,48" fill="var(--paper)"/>
      <polyline points="0,0 300,48 600,0" fill="none" stroke="var(--lime)" stroke-width="5"/>
    </svg>
    <p class="holder-name">DANIEL MARLOWE</p>

    <div class="brand">
      <span class="brand__mark"></span>
      <span class="brand__name">Harbor Builders</span>
    </div>

    <div class="divider"></div>

    <div class="contact">
      <p class="contact__company">Harbor Builders Pty Ltd</p>
      <p>PO Box 2840 Eastgate</p>
      <p>LPO Redvale WA 6099</p>
      <div class="contact__gap"></div>
      <p>Registration 48213</p>
      <p>ABN: 42 305 918 664</p>
      <p class="contact__row contact__row--first">
        <svg viewBox="0 0 13 13" aria-hidden="true"><rect x="3" y="0.5" width="7" height="12" rx="1.2" fill="none" stroke="var(--ink)" stroke-width="1.5"/><rect x="5.5" y="10" width="2" height="1.2" fill="var(--ink)"/></svg>
        0400 555 318
      </p>
      <p class="contact__row">
        <svg viewBox="0 0 13 13" aria-hidden="true"><rect x="1" y="3" width="11" height="7.5" fill="var(--ink)"/><polyline points="1,3 6.5,7.5 12,3" fill="none" stroke="var(--paper)" stroke-width="1"/></svg>
        daniel@harborbuilders.com.au
      </p>
      <p class="contact__row">
        <svg viewBox="0 0 13 13" aria-hidden="true"><circle cx="6.5" cy="6.5" r="5.8" fill="var(--ink)"/><ellipse cx="6.5" cy="6.5" rx="2.4" ry="5.8" fill="none" stroke="var(--paper)" stroke-width="0.8"/><line x1="0.7" y1="6.5" x2="12.3" y2="6.5" stroke="var(--paper)" stroke-width="0.8"/></svg>
        www.harborbuilders.com.au
      </p>
    </div>
  </section>

  <section class="card card--back">
    <div class="back-name">
      <span class="back-name__mark"></span>
      <span class="back-name__text">Harbor Builders</span>
    </div>
    <p class="back-web">www.harborbuilders.com.au</p>
  </section>
</body>
</html>
```